Business Card Design - Amberfield Court

We are looking at a new design for our business cards that has a modern and professional look. We run a residential aged care facility focussing on the care of residents. The cards will be used for potential clients, consultants and business opportunities in this sector. Blue and white is our main colours and would to see these colours incorporated in the design.
Industry/Entity Type
Business
Contact Information for Business Card
Amberfield Court, Darren Walsh, dwalsh@amberfieldcourt.com.au, Finance Manager, 0472 639 208, BCom, 37 Marrabel Crescent, Brindle Vale, Qld 4093.
Look and feel
Each slider illustrates characteristics of the customer's brand and the style your logo design should communicate.

```html
<!DOCTYPE html>
<html lang="en">
<head>
<meta charset="utf-8">
<title>Amberfield Court – Business Card</title>
<link rel="stylesheet" href="https://fonts.googleapis.com/css2?family=Oswald:wght@500&family=Open+Sans:wght@400;600;700&display=swap">
<style>
  :root {
    --bg: #ece9e4;
    --card: #ffffff;
    --brand-blue: #4f7b96;
    --brand-blue-light: #6f98b1;
    --text-blue: #6a8ba0;
    --text-dark: #3e5566;
  }
  * { margin: 0; padding: 0; box-sizing: border-box; }
  html, body {
    width: 1200px; height: 1023px; overflow: hidden;
    background: var(--bg);
    font-family: "Open Sans", Arial, sans-serif;
  }
  .card {
    position: absolute;
    width: 540px; height: 310px;
    background: var(--card);
    box-shadow: 0 6px 18px rgba(0,0,0,0.12);
    overflow: hidden;
  }

  /* Contact side */
  .card-contact { left: 70px; top: 150px; }
  .contact-art {
    position: absolute; left: 0; bottom: 0;
    width: 380px; height: 170px;
  }
  .contact-details {
    position: absolute; right: 34px; top: 30px;
    text-align: right; color: var(--text-blue);
    font-size: 13px; line-height: 1.65;
  }
  .person-name {
    font-family: "Oswald", "Arial Narrow", sans-serif;
    font-weight: 500; font-size: 21px; letter-spacing: 0.5px;
    color: var(--text-dark); text-transform: uppercase; line-height: 1.2;
  }
  .person-role { font-size: 12.5px; margin-bottom: 6px; }
  .contact-line {
    display: flex; justify-content: flex-end; align-items: center; gap: 6px;
    white-space: nowrap;
  }
  .contact-line svg { width: 12px; height: 12px; fill: var(--text-dark); flex-shrink: 0; }
  .company-name { font-weight: 700; color: var(--text-dark); margin-top: 6px; }

  /* Brand side */
  .card-brand { left: 600px; top: 560px; }
  .brand-lockup {
    position: absolute; left: 50%; top: 50%;
    transform: translate(-50%, -50%);
    display: flex; align-items: center; gap: 14px;
    white-space: nowrap;
  }
  .brand-dot {
    width: 40px; height: 40px; border-radius: 50%;
    background: var(--brand-blue);
    flex-shrink: 0;
  }
  .brand-name {
    font-family: "Open Sans", Arial, sans-serif;
    font-weight: 600; font-size: 30px; letter-spacing: 0.5px;
    color: var(--brand-blue);
  }
</style>
</head>
<body>
  <section class="card card-contact">
    <svg class="contact-art" viewBox="0 0 380 170" role="img" aria-label="Large blue silhouette decoration of a carer with a resident">
      <defs>
        <linearGradient id="artFill" x1="0" y1="0" x2="1" y2="1">
          <stop offset="0" stop-color="#6f98b1"/>
          <stop offset="1" stop-color="#4f7b96"/>
        </linearGradient>
      </defs>
      <path d="M0 170 L0 120 Q70 40 180 22 Q290 6 345 60 Q380 100 380 170 Z" fill="url(#artFill)"/>
    </svg>
    <div class="contact-details">
      <div class="person-name">Darren Walsh</div>
      <div class="person-role">Finance Manager</div>
      <div class="contact-line">dwalsh@amberfieldcourt.com.au
        <svg viewBox="0 0 12 12"><rect x="0" y="2" width="12" height="8" rx="1"/></svg>
      </div>
      <div class="contact-line">0472 639 208
        <svg viewBox="0 0 12 12"><path d="M2 0h3l1 3-2 1a7 7 0 0 0 4 4l1-2 3 1v3a2 2 0 0 1-2 2A10 10 0 0 1 0 2a2 2 0 0 1 2-2z"/></svg>
      </div>
      <div class="company-name">Amberfield Court</div>
      <div>BCom, 37 Marrabel Crescent</div>
      <div>Brindle Vale, Qld 4093</div>
    </div>
  </section>

  <section class="card card-brand">
    <div class="brand-lockup">
      <span class="brand-dot"></span>
      <span class="brand-name">Amberfield Court</span>
    </div>
  </section>
</body>
</html>
```